Snapnook needs You

Help us create an inviting, amazing, sleek, simple, clear landing page for a picture-memory-social connection site!

Business Name: SnapNook
Industry: Social Networking and Creativity through Pictures
A web platform for and about a community that is driven by a passion for sharing, caring, bonding, collaborating, creating and earning with pictures, through pictures and other related creative activities. This is going to be a great site for all creative artists-photographers, artists, graphic artists to express their work and their creativity.

The main focus of the site is - CONNECTIONS.
This will be uncoded.

Desired Website Screen Size
1024x768... Widescreen/Landscape orientation, is what we mean... So it fits on a CPU screen.

Desired look and feel and message
Look: Visitor should feel immersed in the page, in the world the page creates, simple, elegant, sophisticated, contemporary. We really like a clean uncluttered look.

Special mention: By the way we love the marketing genius who thought up this branding for velu yogurt where they used the two dots above the o to create a branding effect that made this brand instantly identifiable. http://www.velu-dairy.ca/en/

The two dots by themselves without having even the name present brings up the whole brand now. The dots are used above all the ingredients of the yogurt creating friendly figures, and above people in commercials-bringing the people onto the side of "team" velu. Snapnook may have a character created or something distinctive in the letters in the name created to brand the site as well.

Feel: Engaging; Magical without being corny, here is a link to give an example look and feel but please do not be hindered in your creativity by this suggestion. We love all creative angles.
http://artscrapyard.com/graphic/5829317-camera-film-roll-blue-background

Message: Life and memories and connections through pictures.

Target audience:
The site is focused on pictures but not confined to photography enthusiasts (although they are an integral part of the site). Customers/Visitors will include families, corporates and the younger generation - all age groups, all class, everyone with pictures to express, memories to share.

Website design we like:
http://brindlework.com/work/northern-ballet-house/
http://brindlework.com/work/zapverse/

What colors do we want to see on our landing page?
We would like the background to be grey or blue since it is grey is picture neutral colour and blue highlights pictures well and we also like blue and silver, which can be integrated into the theme. Also like green. But please do not let these instructions limit your creativity. We are open to new ideas and colours.

Predetermined Concepts if any:
We have a concept in mind and we think it would be cool to have an interface for the user through the back of a camera on the landing page -This could be used to create a scene or world the visitor feels a part of or is immersed into. The back screen of the camera may act as a screen for the slideshow of featured pictures on the site.

Content on the Page:
Photo Gallery with full screen, thumbnail view, zoom option etc.
Prominent but short introductory message
Sign in / Login Options
Links: Home Page; About; Info/Help; Contact Us; Privacy Policy; Terms of Use
At the bottom of the page: Follow Me/Like/Workplaza...social buttons.

Please feel free to add any other element to the landing page that you think might add to the effect of simple yet amazing look -clean, simple, uncluttered, sophisticated, stylish, inviting and engaging.
The concept is a guideline, but we would like you to be as creative as you can, even if it meant stepping out of these guidelines - rethink design, style, content if you like. We believe in bringing a solution in an innovative yet simple and elegant style. Something a visitor would be intrigued enough to explore and the guest would feel comfortable enough taking that step forward to have fun on the site. If you believe in the same, and you have the skill then you will have what we need. Good luck, go for it and we are excited to see what the amazing designers on this amazing site have to offer.
If you have any questions please free to ask.

HI wanted to send an update that this project design has been guaranteed.

Our site will be one to celebrate and showcase imagination as well as connection.  We would love to see what you create. Keep in mind our site will showcase all creativity, photographs, artists, graphic artists so this would be a benefit you may want to take advantage of in the future, a place where, if you so choose, you could gain exposure for your work. Therefore, even if you do not win the design project there is possible future benefit.

Imagination is everything.
Imagination encircles the world.-Halvorsen

Reason: We are giving the designers who accepted invites but have not yet submitted a chance to finish their submissions and the ones who are working on revisions a chance to finish those:)

Hello everyone,

Due to time constraints we must come to a decision sooner than the deadline of 28th. 

So, please try to submit any new designs or modifications to the old ones before the 26th. We are very thankful to all of you who have participated - for your designs, enthusiasm and kind words. 

Good luck! :)

• Thank you for the interest shown and your submissions! Designers who have submitted up until now have shown great potential. We are VERY excited with the quality of work and designs.

We want to add that Snapnook is not exclusively for the photographers. The site is for every person who may have a picture to store, organise, use or share - whether publicly or with only a few friends and family.

Snapnook is about allowing people to take control of their creativity. It is about providing tools to our users so that they can build their own connections and social network... of friends, family, fans, clients, ideas, thoughts, emotions etc. through pictures without worrying about their privacy or control over their creations.

With this update we want to encourage others to go beyond the camera theme. Do not let us restrict your creativity. Let YOUR OWN ideas take over if that’s what you think will best convey the message and will appeal to the users.

```html
<!DOCTYPE html>
<html lang="en">
<head>
<meta charset="utf-8">
<title>SnapNook — Photos Online</title>
<link rel="stylesheet" href="https://fonts.googleapis.com/css2?family=Arimo:ital,wght@0,400;0,700;1,400;1,700&display=swap">
<style>
  :root{
    --strip:#ffffff;
    --stage-top:#c4c4c4;
    --stage-mid:#dcdcdc;
    --brand-blue:#1d5fa8;
    --ink:#111111;
    --band-top:#1e6cc2;
    --band-bottom:#22e8fc;
    --white:#ffffff;
    --pale:#e8f1fa;
    --navy:#0c2a78;
    --navy-btn:#0a2370;
    --field:#ffffff;
  }
  *{margin:0;padding:0;box-sizing:border-box}
  html,body{width:1200px;height:601px;overflow:hidden;background:var(--white)}
  body{font-family:"Arimo",Arial,sans-serif;position:relative}
  .page{position:relative;width:1200px;height:601px;overflow:hidden}

  .top-strip{position:absolute;left:0;top:0;width:1200px;height:7px;background:var(--strip)}
  .stage{position:absolute;left:0;top:7px;width:1200px;height:383px;
    background:radial-gradient(ellipse at 50% 55%,var(--stage-mid) 0%,var(--stage-top) 75%)}
  .band{position:absolute;left:0;top:390px;width:1200px;height:211px;
    background:linear-gradient(180deg,var(--band-top) 0%,#1f9ee0 40%,var(--band-bottom) 100%)}

  .social{position:absolute;left:777px;top:7px;display:flex;gap:1px}
  .social span{width:14px;height:14px;border-radius:2px;display:block}
  .social .s1{background:#3b5fa6}.social .s2{background:#d9d9d9}
  .social .s3{background:#f08a1d}.social .s4{background:#2fb52f}

  .logo{position:absolute;left:229px;top:42px;font-size:29px;font-weight:400;
    color:var(--brand-blue);letter-spacing:.5px}
  .tagline{position:absolute;left:566px;top:48px;font-size:12px;font-style:italic;color:var(--ink)}
  .search-icon{position:absolute;left:709px;top:46px}
  .search{position:absolute;left:739px;top:44px;width:157px;height:19px;background:var(--field);
    border-radius:4px;font-size:12.5px;font-style:italic;color:var(--brand-blue);padding:2px 6px}

  .photo{position:absolute}
  .photo-side-left{left:0;top:133px;width:209px;height:185px;opacity:.45;
    background:linear-gradient(135deg,#a99a62,#b48a78 55%,#8e8a5a)}
  .photo-side-right{left:920px;top:119px;width:280px;height:190px;opacity:.55;
    background:linear-gradient(180deg,#d6dcdf,#a9b2b6 60%,#8f999d)}
  .photo-main{left:347px;top:109px;width:437px;height:234px;
    background:linear-gradient(160deg,#bfe0f5 0%,#e9f3fa 35%,#5f87a8 60%,#f2f7fb 85%)}

  .arrow{position:absolute;width:22px;height:22px}
  .arrow-prev{left:271px;top:216px}
  .arrow-next{left:828px;top:213px}

  .nav{position:absolute;left:245px;top:407px;display:flex;align-items:center;
    font-size:12px;color:var(--white);list-style:none}
  .nav li{display:flex;align-items:center}
  .nav .sep{margin:0 11px;font-size:15px;opacity:.85}

  .signin-label{position:absolute;left:243px;top:447px;font-size:22px;font-style:italic;color:var(--white)}
  .signin-field{position:absolute;left:334px;top:451px;width:134px;height:18px;background:var(--field);border-radius:3px}
  .signin-note{position:absolute;left:243px;top:487px;font-size:11px;font-style:italic;color:var(--white);line-height:12px}
  .trial{position:absolute;left:243px;top:535px;font-size:14px;font-style:italic;color:var(--navy);word-spacing:3px}
  .signup{position:absolute;left:335px;top:532px;width:78px;height:21px;background:var(--navy-btn);
    border-radius:3px;color:var(--white);font-size:13px;font-style:italic;text-align:center;line-height:21px}

  .intro-title{position:absolute;left:612px;top:424px;font-size:26px;font-weight:700;font-style:italic;color:var(--pale)}
  .intro-text{position:absolute;left:615px;top:461px;width:330px;font-size:13.5px;font-style:italic;
    line-height:15.2px;color:var(--pale)}
  .intro-brand{position:absolute;left:615px;top:545px;font-size:14px;color:var(--white)}
</style>
</head>
<body>
<div class="page">
  <div class="top-strip"></div>
  <div class="stage"></div>
  <div class="band"></div>

  <div class="social" aria-label="Social links">
    <span class="s1"></span><span class="s2"></span><span class="s3"></span><span class="s4"></span>
  </div>

  <div class="logo">SNAPNOOK</div>
  <div class="tagline">PROFESHIONAL PHTO</div>
  <svg class="search-icon" width="16" height="16" viewBox="0 0 16 16" aria-hidden="true">
    <circle cx="10" cy="6" r="4" fill="none" stroke="#1b8fd6" stroke-width="2"/>
    <line x1="7" y1="9" x2="2" y2="14" stroke="#1b5fa6" stroke-width="2.4" stroke-linecap="round"/>
  </svg>
  <div class="search">Search</div>

  <div class="photo photo-side-left" role="img" aria-label="Faded featured photo: close-up of a chestnut in its spiky husk"></div>
  <div class="photo photo-side-right" role="img" aria-label="Faded featured photo: whale fin in icy grey water"></div>
  <div class="photo photo-main" role="img" aria-label="Featured photo: skier on a snowy mountain slope above a valley river"></div>

  <svg class="arrow arrow-prev" viewBox="0 0 22 22" aria-label="Previous photo">
    <circle cx="11" cy="11" r="11" fill="#f4f4f4"/>
    <path d="M13 6 L8 11 L13 16" fill="none" stroke="#6a6a6a" stroke-width="2.4"/>
  </svg>
  <svg class="arrow arrow-next" viewBox="0 0 22 22" aria-label="Next photo">
    <circle cx="11" cy="11" r="11" fill="#f4f4f4"/>
    <path d="M9 6 L14 11 L9 16" fill="none" stroke="#6a6a6a" stroke-width="2.4"/>
  </svg>

  <ul class="nav">
    <li>home</li><li class="sep">/</li>
    <li>products</li><li class="sep">/</li>
    <li>about</li><li class="sep">/</li>
    <li>contact</li>
  </ul>

  <div class="signin-label">SIGN IN</div>
  <div class="signin-field"></div>
  <p class="signin-note">&nbsp;Liber primis maiestatis ius<br>ut. Ius liber congue laboramus ne.</p>
  <div class="trial">FREE TRIAL</div>
  <div class="signup">SIGN UP</div>

  <h1 class="intro-title">PHOTOS ONLINE</h1>
  <p class="intro-text">Te dicam labitur mel, est eu graeco minimum, in sit facer assueverit inciderint. Laudem diceret no his, et mea minim nominati democritum, at quo partem numquam feugiat. Liber primis maiestatis ius ut. Ius liber congue laboramus ne.</p>
  <div class="intro-brand">SNAPNOOK</div>
</div>
</body>
</html>
```